Unique Business Card Design

Unique Business Card design for our orthotic and prosthetic company. Our logo is on our website, color is light blue. Unique shape (artificial leg shaped, vertical, etc..) preferred. Logo, business name, individual name and basic demographics needed.

Industry/Entity Type

Business

Contact Information for Business Card

Logo, Industry, Phone # Logo, "Prosthetic & Orthotic Services" Place to add individual name and contact info

Colors
cee9f5

Requirements
Must have
• The icon must be there, placement of "Prosthetic & Orthotic Services" can be moved
Nice to have
• Like the mix of light blue, and a little darker blue. One design included the icons from my website which was a nice touch

```html
<!DOCTYPE html>
<html lang="en">
<head>
<meta charset="utf-8">
<title>Limbworks Co. Business Card</title>
<link rel="stylesheet" href="https://fonts.googleapis.com/css2?family=Open+Sans:ital,wght@0,400;0,600;0,700;1,400&family=Crimson+Text:ital@1&display=swap">
<style>
  :root {
    --stage: #4d4d4d;
    --card: #ffffff;
    --brand-blue: #1a5fae;
    --swoosh-gray: #5a5a5a;
    --ink-gray: #555555;
    --on-blue: #ffffff;
  }
  * { margin: 0; padding: 0; box-sizing: border-box; }
  html, body {
    width: 1105px; height: 1200px; overflow: hidden;
    background: var(--stage);
    font-family: "Open Sans", Arial, sans-serif;
  }
  .card {
    position: absolute; left: 193px; width: 720px; height: 410px;
    border-radius: 24px; overflow: hidden; background: var(--card);
  }
  .card-front { top: 167px; }
  .card-back { top: 623px; }
  .card-art { position: absolute; inset: 0; }

  .brand-mark {
    position: absolute; left: 174px; top: 58px;
    width: 96px; height: 96px; border-radius: 50%; background: var(--brand-blue);
  }
  .brand-name {
    position: absolute; left: 297px; top: 76px;
    font-weight: 700; font-size: 27px; line-height: 1; color: var(--brand-blue);
    letter-spacing: 0.2px;
  }
  .brand-rule {
    position: absolute; left: 298px; top: 111px; width: 240px; height: 2px;
    background: var(--brand-blue);
  }
  .brand-tagline {
    position: absolute; left: 312px; top: 114px;
    font-family: "Crimson Text", Georgia, serif; font-style: italic;
    font-size: 17px; color: var(--brand-blue);
  }

  .person {
    position: absolute; right: 370px; top: 254px; text-align: right; color: var(--on-blue);
  }
  .person-name { font-weight: 700; font-size: 25px; line-height: 30px; letter-spacing: 0.3px; }
  .person-title { font-weight: 700; font-size: 17px; line-height: 24px; margin-bottom: 6px; }
  .person-address { font-size: 18px; line-height: 27px; }

  .divider {
    position: absolute; left: 373px; top: 255px; width: 1px; height: 123px;
    background: var(--on-blue);
  }
  .contact-list { position: absolute; left: 393px; top: 258px; list-style: none; }
  .contact-item {
    display: flex; align-items: center; height: 27.3px;
    font-size: 18px; color: var(--on-blue);
  }
  .contact-icon { width: 18px; height: 18px; margin-right: 10px; fill: var(--on-blue); }

  .back-mark {
    position: absolute; left: 248px; top: 80px; width: 224px; height: 224px;
    border-radius: 50%; background: var(--brand-blue);
    display: flex; align-items: center; justify-content: center;
  }
  .back-mark-name { font-weight: 700; font-size: 24px; color: var(--on-blue); }
  .back-url {
    position: absolute; left: 0; right: 0; top: 342px; text-align: center;
    font-style: italic; font-size: 17px; letter-spacing: 4.5px; color: var(--ink-gray);
  }
</style>
</head>
<body>

<section class="card card-front">
  <svg class="card-art" viewBox="0 0 720 410" aria-hidden="true">
    <path d="M0 182 Q330 222 720 172 L720 182 Q330 230 0 195 Z" fill="var(--swoosh-gray)"/>
    <path d="M0 203 Q360 240 720 186 L720 410 L0 410 Z" fill="var(--brand-blue)"/>
  </svg>

  <div class="brand-mark"></div>
  <div class="brand-name">LIMBWORKS CO.</div>
  <div class="brand-rule"></div>
  <div class="brand-tagline">Prosthetic &amp; Orthotic Services</div>

  <div class="person">
    <div class="person-name">MIRIAM HALPERN</div>
    <div class="person-title">CO LPO</div>
    <div class="person-address">2260 W. 14th St.<br>Newark, NJ 07103</div>
  </div>

  <div class="divider"></div>

  <ul class="contact-list">
    <li class="contact-item">
      <svg class="contact-icon" viewBox="0 0 24 24"><path d="M6.6 10.8a15 15 0 0 0 6.6 6.6l2.2-2.2a1 1 0 0 1 1-.25 11.4 11.4 0 0 0 3.6.57 1 1 0 0 1 1 1V20a1 1 0 0 1-1 1A17 17 0 0 1 3 4a1 1 0 0 1 1-1h3.5a1 1 0 0 1 1 1c0 1.25.2 2.45.57 3.57a1 1 0 0 1-.25 1z"/></svg>
      212.555.0148
    </li>
    <li class="contact-item">
      <svg class="contact-icon" viewBox="0 0 24 24"><path d="M7 1h10a2 2 0 0 1 2 2v18a2 2 0 0 1-2 2H7a2 2 0 0 1-2-2V3a2 2 0 0 1 2-2zm0 3v14h10V4z"/></svg>
      212.555.0193
    </li>
    <li class="contact-item">
      <svg class="contact-icon" viewBox="0 0 24 24"><path d="M6 2h12v6H6zM3 9h18a1 1 0 0 1 1 1v8h-4v4H6v-4H2v-8a1 1 0 0 1 1-1zm5 7v4h8v-4z"/></svg>
      212-5550176
    </li>
    <li class="contact-item">
      <svg class="contact-icon" viewBox="0 0 24 24"><path d="M2 5h20v14H2zm2 2v.5l8 5 8-5V7zm0 3v7h16v-7l-8 5z"/></svg>
      mhalpern@limbworksco.com
    </li>
    <li class="contact-item">
      <svg class="contact-icon" viewBox="0 0 24 24"><path d="M12 2a10 10 0 1 0 0 20 10 10 0 0 0 0-20zm-1 17.9A8 8 0 0 1 4.2 10l4.8 4.8v1a2 2 0 0 0 2 2zm6.9-2.5A2 2 0 0 0 16 16h-1v-3a1 1 0 0 0-1-1H8v-2h2a1 1 0 0 0 1-1V7h2a2 2 0 0 0 2-2v-.4a8 8 0 0 1 2.9 12.8z"/></svg>
      www.limbworksco.com
    </li>
  </ul>
</section>

<section class="card card-back">
  <div class="back-mark"><span class="back-mark-name">LIMBWORKS CO.</span></div>
  <div class="back-url">www.limbworksco.com</div>
</section>

</body>
</html>
```